Lorvex Tilo medical cannibis cultivation company

tag - Tilo rise
Lorvex Tilo medical cannabis cultivation - logo is selected- can we please see bold examples with our selection. We are mainly dealing with medical companies and professionals. We would like to be stand out in the crowd with our designs. Welcome any and all attempts. Thanks

Target Market(s)

Medical and Professional

Industry/Entity Type

Medical And Science

Font styles to use
Sans Serif

Colors

Designer to choose colors to be used in the design.

Requirements
Must have
• Bright colour and be bold- Love the teal and magenta that is currently on the dark background design.
Nice to have
• shading and the 3D affect- The shadowed appearance.
Should not have
• Anything related to illegal activity or un professional manners

```html
<!DOCTYPE html>
<html lang="en">
<head>
<meta charset="utf-8">
<title>Lorvex Tilo — Business Card</title>
<link href="https://fonts.googleapis.com/css2?family=Roboto:wght@400;500;700&display=swap" rel="stylesheet">
<style>
  :root {
    --page: #e9e6e1;
    --card: #000000;
    --teal: #00a9e6;
    --magenta: #9b45a0;
    --grey: #8d9196;
    --text: #e8e8e8;
  }
  * { box-sizing: border-box; margin: 0; padding: 0; }
  html, body { width: 1125px; height: 1200px; overflow: hidden; }
  body {
    background: var(--page);
    font-family: "Roboto", Arial, sans-serif;
    position: relative;
  }
  .card {
    position: absolute;
    left: 150px;
    width: 825px;
    height: 470px;
    background: var(--card);
    border-radius: 26px;
    overflow: hidden;
    box-shadow: 0 10px 24px rgba(0,0,0,0.35);
  }
  .card--front { top: 98px; }
  .card--back { top: 630px; }

  /* front */
  .brand {
    position: absolute;
    left: 40px; top: 110px;
    width: 440px;
    text-align: center;
  }
  .brand__mark {
    width: 92px; height: 92px;
    margin: 0 auto 30px;
    border-radius: 50%;
    border: 5px solid var(--grey);
  }
  .brand__name {
    font-size: 48px;
    font-weight: 700;
    color: var(--teal);
    letter-spacing: 1px;
    line-height: 1;
  }
  .brand__tag {
    margin-top: 14px;
    display: flex;
    align-items: center;
    justify-content: center;
    gap: 10px;
    color: var(--grey);
    font-size: 20px;
    letter-spacing: 2px;
    text-transform: uppercase;
  }
  .brand__tag::before, .brand__tag::after {
    content: "";
    width: 60px; height: 2px;
    background: var(--grey);
  }
  .divider {
    position: absolute;
    left: 448px; top: 80px;
    width: 3px; height: 300px;
    background: linear-gradient(to bottom, transparent, #9a9a9a 20%, #9a9a9a 80%, transparent);
  }
  .contact {
    position: absolute;
    left: 492px; top: 96px;
    color: var(--text);
  }
  .contact__name {
    font-size: 29px; font-weight: 500;
    color: var(--teal);
    letter-spacing: 0.5px;
  }
  .contact__role {
    font-size: 20px; font-weight: 500;
    color: var(--magenta);
    margin-top: 2px;
  }
  .contact__address {
    font-size: 19px;
    line-height: 25px;
    margin-top: 16px;
  }
  .contact__list {
    list-style: none;
    margin-top: 14px;
    font-size: 19px;
  }
  .contact__list li {
    display: flex; align-items: center; gap: 10px;
    height: 26px;
  }
  .contact__list svg { width: 20px; height: 20px; fill: var(--teal); flex: none; }
  .band {
    position: absolute;
    left: 0; right: 0; bottom: 0;
    height: 17px;
    background: linear-gradient(100deg, var(--teal) 0 60.5%, #1a1a1a 60.5% 61%, var(--magenta) 61%);
  }

  /* back */
  .emblem {
    position: absolute;
    left: 282px; top: 95px;
    width: 260px; height: 260px;
    border-radius: 50%;
    border: 6px solid var(--grey);
    display: flex; align-items: center; justify-content: center;
  }
  .emblem__name {
    font-size: 34px; font-weight: 700;
    color: var(--teal);
    letter-spacing: 1px;
  }
  .site {
    position: absolute;
    left: 0; right: 0; top: 395px;
    text-align: center;
    color: var(--text);
    font-size: 20px;
    letter-spacing: 5px;
  }
</style>
</head>
<body>
  <section class="card card--front">
    <div class="brand">
      <div class="brand__mark"></div>
      <div class="brand__name">LORVEX TILO</div>
      <div class="brand__tag">Tilo rise</div>
    </div>
    <div class="divider"></div>
    <div class="contact">
      <div class="contact__name">MAREN HOLT</div>
      <div class="contact__role">CEO/FOUNDER</div>
      <div class="contact__address">2140 Fenwick Row<br>Dellmoor, Ashvale 58213</div>
      <ul class="contact__list">
        <li><svg viewBox="0 0 24 24"><path d="M6.6 10.8a15.1 15.1 0 0 0 6.6 6.6l2.2-2.2c.3-.3.7-.4 1-.2 1.1.4 2.3.6 3.6.6.6 0 1 .4 1 1V20c0 .6-.4 1-1 1C10.6 21 3 13.4 3 4c0-.6.4-1 1-1h3.5c.6 0 1 .4 1 1 0 1.3.2 2.5.6 3.6.1.3 0 .7-.2 1z"/></svg>555 201 4470</li>
        <li><svg viewBox="0 0 24 24"><path d="M7 1h10a2 2 0 0 1 2 2v18a2 2 0 0 1-2 2H7a2 2 0 0 1-2-2V3a2 2 0 0 1 2-2zm0 3v14h10V4zm5 15.5a1 1 0 1 0 0 2 1 1 0 0 0 0-2z"/></svg>555 386 1192</li>
        <li><svg viewBox="0 0 24 24"><path d="M6 2h9l3 3v5H6zm-2 9h16a2 2 0 0 1 2 2v7H2v-7a2 2 0 0 1 2-2zm2 4v2h4v-2zm8 0v2h2v-2z"/></svg>555 742 6035</li>
        <li><svg viewBox="0 0 24 24"><path d="M2 5h20v14H2zm2 2v.4l8 5.3 8-5.3V7zm0 2.8V17h16V9.8l-8 5.3z"/></svg>maren@lorvextilo.com</li>
        <li><svg viewBox="0 0 24 24"><path d="M12 2a10 10 0 1 0 0 20 10 10 0 0 0 0-20zm-1 17.9A8 8 0 0 1 4.2 10L9 14.8v1.2a2 2 0 0 0 2 2zm6.9-2.5A2 2 0 0 0 16 16h-1v-3a1 1 0 0 0-1-1H8v-2h2a1 1 0 0 0 1-1V7h2a2 2 0 0 0 2-2v-.4a8 8 0 0 1 2.9 12.8z"/></svg>www.lorvextilo.com</li>
      </ul>
    </div>
    <div class="band"></div>
  </section>

  <section class="card card--back">
    <div class="emblem">
      <span class="emblem__name">LORVEX TILO</span>
    </div>
    <div class="site">www.lorvextilorise.com</div>
  </section>
</body>
</html>
```